Meadow Kr Circle (company name is Meadow Kr Circle LLP)

management of homestay, hospitality something similar with https://www.dorvika.example

Target Market(s)

johor bahru market (Malaysia)

Contact Information for Business Card

Meadow Circle KR LLP

Logo Text

eyes catching, attractive, amazing, Nice, jaw dropping for design

Coding

Coded - Design and coding required

Number of Pages Required

5+ page

Colors

Designer to choose colors to be used in the design.

Requirements
Must have
• please change the short term proposal to our company logo and change the name from dorvika to meadow KR Circle LLP
• thanks
Nice to have
• please let me have eyes catching , jaw dropping design

```html
<!DOCTYPE html>
<html lang="en">
<head>
<meta charset="utf-8">
<title>Meadow Kr Circle — Hospitality Management</title>
<link rel="stylesheet" href="https://fonts.googleapis.com/css2?family=Montserrat:wght@600;700;800&family=Roboto:wght@400;500;700&display=swap">
<style>
:root{
  --teal:#177079;
  --teal-dark:#12525a;
  --teal-bright:#1b8a92;
  --coral:#f0555c;
  --ink:#222629;
  --text:#6b7075;
  --line:#d9dcde;
  --white:#ffffff;
  --pale:#f3f5f6;
}
*{box-sizing:border-box;margin:0;padding:0}
html,body{width:1200px;height:3854px;overflow:hidden}
body{position:relative;background:var(--white);font-family:"Roboto",Arial,sans-serif;color:var(--text)}
.abs{position:absolute}
.heading{font-family:"Montserrat",Arial,sans-serif;font-weight:800;color:var(--ink);text-transform:uppercase;letter-spacing:-.5px}

/* header */
.top-rule{left:0;top:0;width:1200px;height:4px;background:var(--coral)}
.site-header{left:0;top:4px;width:1200px;height:132px;background:var(--white)}
.brand{left:110px;top:38px;display:flex;align-items:center;gap:14px}
.brand-dot{width:46px;height:46px;border-radius:50%;background:var(--teal)}
.brand-name{font-family:"Montserrat",Arial,sans-serif;font-weight:700;font-size:24px;color:var(--teal)}
.main-nav{right:112px;top:62px;display:flex;gap:26px;font-family:"Roboto",Arial,sans-serif;font-weight:500;font-size:13px;color:var(--ink)}
.main-nav .active{color:var(--teal-bright)}

/* hero */
.hero{left:0;top:136px;width:1200px;height:560px;background:linear-gradient(100deg,#eef0ef 0%,#dcd8d2 35%,#8d8278 62%,#4c4742 100%)}
.hero-title{left:110px;top:286px;font-size:45px;line-height:58px;color:var(--teal);letter-spacing:-.5px}
.btn-pill{display:flex;align-items:center;justify-content:center;gap:6px;border-radius:24px;font-family:"Roboto",Arial,sans-serif;font-weight:700;font-size:13px;text-transform:uppercase}
.btn-solid{background:var(--coral);color:var(--white)}
.btn-outline{border:2px solid #e7c9ca;color:var(--coral);background:rgba(255,255,255,.6)}
.hero .btn-pill{position:absolute}

/* about */
.about-bg{left:0;top:696px;width:1200px;height:1252px;background:linear-gradient(180deg,#f6f8f8 0%,#ffffff 40%,#f4f6f7 70%,#eef1f2 100%)}
.about-photo{left:110px;top:833px;width:455px;height:306px;border:5px solid var(--white);box-shadow:0 2px 10px rgba(0,0,0,.15);background:linear-gradient(120deg,#c9c3b8,#e7e2da 45%,#8aa3b2)}
.section-title{display:flex;align-items:center;gap:14px;font-size:40px}
.title-dot{width:40px;height:40px;border-radius:50%;background:var(--teal)}
.about-copy{left:630px;top:910px;width:460px;font-size:13px;line-height:26px}
.about-copy p+p{margin-top:22px}
.divider{left:110px;top:1254px;width:980px;height:1px;background:var(--line)}

/* services */
.services-sub{left:0;top:1448px;width:1200px;text-align:center;font-size:18px;color:#4a4f53;letter-spacing:.5px}
.service-card{top:1509px;width:304px}
.service-img{width:304px;height:185px}
.service-card h3{margin-top:32px;font-family:"Roboto",Arial,sans-serif;font-weight:700;font-size:18px;line-height:30px;color:var(--ink)}
.service-card p{margin-top:14px;font-size:12.5px;line-height:24px}

/* activities band */
.activity-band{left:0;top:1948px;width:1200px;height:332px;background:linear-gradient(90deg,var(--teal) 0%,#1a7982 50%,var(--teal) 100%)}
.activity{top:2040px;width:220px;text-align:center}
.activity-ring{width:112px;height:112px;margin:0 auto;border-radius:50%;background:var(--white);display:flex;align-items:center;justify-content:center}
.activity-art{width:64px;height:64px;border-radius:50%}
.activity-label{margin-top:26px;font-family:"Montserrat",Arial,sans-serif;font-weight:700;font-size:22px;color:var(--white);letter-spacing:.5px}

/* blog */
.pager{left:816px;top:2416px;display:flex;align-items:center;gap:14px}
.pager-dot{width:36px;height:36px;border-radius:50%;background:#dde2e3;color:var(--teal);font-weight:700;font-size:17px;display:flex;align-items:center;justify-content:center}
.pager-dot.current{background:var(--teal);color:var(--white)}
.pager-gap{font-size:18px;letter-spacing:4px;color:var(--teal)}
.post-img{left:110px;width:396px;height:262px}
.date-badge{width:66px;height:66px;border-radius:50%;background:var(--teal);border:3px solid var(--white);color:var(--white);text-align:center;font-family:"Montserrat",Arial,sans-serif;font-weight:700;line-height:1}
.date-badge b{display:block;font-size:22px;margin-top:11px}
.date-badge span{font-size:12px;letter-spacing:1px}
.post-body{left:578px;width:512px}
.post-body h3{font-family:"Roboto",Arial,sans-serif;font-weight:700;font-size:22px;line-height:36px;color:var(--ink)}
.post-body p{margin-top:22px;font-size:12.5px;line-height:24px}
.post-body .btn-pill{margin-top:28px;width:172px;height:46px}

/* newsletter */
.newsletter{left:0;top:3225px;width:1200px;height:185px;background:var(--coral)}
.newsletter h2{position:absolute;left:110px;top:68px;font-family:"Montserrat",Arial,sans-serif;font-weight:700;font-size:24px;color:var(--white);text-transform:uppercase}
.newsletter p{position:absolute;left:110px;top:108px;font-size:12.5px;color:#ffe3e4}
.news-field{position:absolute;left:694px;top:72px;width:291px;height:42px;background:var(--white);font-size:13px;color:#555;padding:13px 18px}
.news-btn{position:absolute;left:985px;top:72px;width:103px;height:42px;background:var(--teal-dark);color:var(--white);font-weight:700;font-size:15px;display:flex;align-items:center;justify-content:center;text-transform:uppercase}

/* footer */
.site-footer{left:0;top:3410px;width:1200px;height:444px;background:linear-gradient(180deg,#176e77,#135f67)}
.foot-title{font-family:"Montserrat",Arial,sans-serif;font-weight:700;font-size:17px;color:var(--white);text-transform:uppercase}
.contact-list{left:110px;top:3556px;width:250px;list-style:none;color:#e6f0f1;font-size:13px;line-height:20px}
.contact-list li{display:flex;gap:16px;margin-bottom:22px}
.contact-list svg{flex:none;margin-top:2px}
.field{border:1px solid #c9dcde;color:#eef5f5;font-size:12px;padding:10px 14px}
.submit{left:398px;top:3690px;width:98px;height:34px;border-radius:18px;background:var(--coral);color:var(--white);font-weight:700;font-size:13px;display:flex;align-items:center;justify-content:center;text-transform:uppercase}
.map{left:781px;top:3516px;width:307px;height:206px;border:4px solid var(--white);background:linear-gradient(135deg,#eef0ee,#dfe6e2 50%,#e9e4dc)}
.map-tag{position:absolute;left:14px;top:14px;background:var(--white);color:var(--coral);font-size:12px;font-weight:700;padding:6px 12px;box-shadow:0 1px 4px rgba(0,0,0,.2)}
.foot-rule{left:110px;top:3778px;width:980px;height:1px;background:rgba(255,255,255,.25)}
.copyright{left:110px;top:3808px;font-size:13px;color:#e6f0f1}
.social{left:914px;top:3800px;display:flex;gap:13px}
.social span{width:33px;height:33px;border-radius:50%;border:2px solid var(--white)}
</style>
</head>
<body>

<div class="abs top-rule"></div>
<header class="abs site-header">
  <div class="abs brand"><div class="brand-dot"></div><div class="brand-name">Meadow Kr Circle</div></div>
  <nav class="abs main-nav">
    <span class="active">HOME</span><span>OUR SERVICES</span><span>ABOUT US</span><span>BLOG</span><span>OUR STORY</span><span>CONTACT US</span>
    <svg width="14" height="14" viewBox="0 0 14 14"><circle cx="6" cy="6" r="4.5" fill="none" stroke="#222629" stroke-width="2"/><line x1="9.5" y1="9.5" x2="13" y2="13" stroke="#222629" stroke-width="2"/></svg>
  </nav>
</header>

<section class="abs hero" role="img" aria-label="Bright modern living room with sofa, stone feature wall and fireplace">
</section>
<h1 class="abs heading hero-title">Maximize your<br>home rental income</h1>
<a class="abs btn-pill btn-solid" style="left:110px;top:434px;width:188px;height:42px">Get started
  <svg width="12" height="12" viewBox="0 0 12 12"><circle cx="6" cy="6" r="6" fill="#fff"/><path d="M5 3.5 7.5 6 5 8.5" fill="none" stroke="#f0555c" stroke-width="1.6"/></svg></a>

<div class="abs about-bg"></div>
<div class="abs about-photo" role="img" aria-label="Couple meeting an agent at a desk"></div>
<h2 class="abs heading section-title" style="left:630px;top:818px"><span class="title-dot"></span>About us</h2>
<div class="abs about-copy">
  <p>We are a short-term rental management and provides hospitality services to help property owners maximize their rental income.</p>
  <p>Our goal is to help you reap the most from your rental income without you having to do any of the hard work such as handle all the particular renting problems on Roomnest, Stayfinder, cleaning and dealing with tenants and guests.</p>
</div>
<a class="abs btn-pill btn-outline" style="left:632px;top:1097px;width:168px;height:44px">Read more
  <svg width="12" height="12" viewBox="0 0 12 12"><circle cx="6" cy="6" r="6" fill="#f0555c"/><path d="M5 3.5 7.5 6 5 8.5" fill="none" stroke="#fff" stroke-width="1.6"/></svg></a>
<div class="abs divider"></div>

<h2 class="abs heading section-title" style="left:0;top:1352px;width:1200px;justify-content:center"><span class="title-dot"></span>Our services</h2>
<div class="abs services-sub">Our Hassle-Free Full Hospitality Service For you.</div>

<article class="abs service-card" style="left:110px">
  <div class="service-img" role="img" aria-label="Calculator and small model house" style="background:linear-gradient(135deg,#2c3e55,#7b93b3 55%,#dfe7ef)"></div>
  <h3>Answering Enquiries, Check-Ins / Check-Outs</h3>
  <p>We will answer all guest's enquiries, meet them to handover key and verification check. We also provide 24hr on-call support.</p>
</article>
<article class="abs service-card" style="left:447px">
  <div class="service-img" role="img" aria-label="Gloved hand cleaning a table" style="background:linear-gradient(135deg,#5a4a3a,#b79a6c 55%,#e8d36a)"></div>
  <h3>Full Cleaning, Laundry and Maintenance</h3>
  <p>We get the professional cleaning team to clean up the place after the guest checked-out every time.</p>
</article>
<article class="abs service-card" style="left:784px">
  <div class="service-img" role="img" aria-label="Hand holding a model house above coins" style="background:linear-gradient(135deg,#d9dde0,#9fa8ae 55%,#c2563f)"></div>
  <h3>Marketing And Optimization Services</h3>
  <p>We take professional photos and write persuasive copywriting to optimize your listing in order to get more booking.</p>
</article>

<section class="abs activity-band">
  <svg class="abs" style="left:46px;top:148px" width="20" height="36" viewBox="0 0 20 36"><path d="M17 3 4 18l13 15" fill="none" stroke="#fff" stroke-width="3"/></svg>
  <svg class="abs" style="left:1134px;top:148px" width="20" height="36" viewBox="0 0 20 36"><path d="M3 3l13 15L3 33" fill="none" stroke="#fff" stroke-width="3"/></svg>
</section>
<div class="abs activity" style="left:72px"><div class="activity-ring"><div class="activity-art" role="img" aria-label="Travel planner icon" style="background:#e8513e"></div></div><div class="activity-label">TRAVEL TIPS</div></div>
<div class="abs activity" style="left:355px"><div class="activity-ring"><div class="activity-art" role="img" aria-label="Spa stones icon" style="background:#4a4f53"></div></div><div class="activity-label">BEAUTY SERVICES</div></div>
<div class="abs activity" style="left:638px"><div class="activity-ring"><div class="activity-art" role="img" aria-label="Activities icon" style="background:#3f4a48"></div></div><div class="activity-label">ACTIVITIES</div></div>
<div class="abs activity" style="left:892px"><div class="activity-ring"><div class="activity-art" role="img" aria-label="Party bunting icon" style="background:#e94f4f"></div></div><div class="activity-label">COUPLE PARTY</div></div>

<h2 class="abs heading section-title" style="left:110px;top:2392px"><span class="title-dot"></span>Blog post</h2>
<div class="abs pager">
  <span class="pager-dot current">1</span><span class="pager-dot">2</span><span class="pager-dot">3</span>
  <span class="pager-gap">······</span>
  <span class="pager-dot"><svg width="16" height="16" viewBox="0 0 16 16"><circle cx="8" cy="8" r="8" fill="#177079"/><path d="M4 8h7M8 5l3 3-3 3" fill="none" stroke="#fff" stroke-width="1.8"/></svg></span>
</div>

<div class="abs post-img" style="top:2516px;background:linear-gradient(135deg,#e5e2dc,#a58a6c 55%,#5a4634)" role="img" aria-label="Modern kitchen with wooden island"></div>
<div class="abs date-badge" style="left:473px;top:2614px"><b>18</b><span>DEC</span></div>
<article class="abs post-body" style="top:2506px">
  <h3>Lorem ipsum dolor amet eiusmod consectetur adipiscing elit eiusmod tempor.</h3>
  <p>Lorem ipsum dolor sit amet, consectetur adipiscing elit, sed do eiusmod tempor incididunt ut labore et dolore magna aliqua. Ut enim ad minim veniam, quis nostrud exercitation ullamco laboris nisi ut aliquip ex ea commodo consequat. Duis aute irure dolor in reprehenderit in voluptate velit esse cillum dolore...</p>
  <a class="btn-pill btn-outline">Read more <svg width="12" height="12" viewBox="0 0 12 12"><circle cx="6" cy="6" r="6" fill="#f0555c"/><path d="M5 3.5 7.5 6 5 8.5" fill="none" stroke="#fff" stroke-width="1.6"/></svg></a>
</article>

<div class="abs post-img" style="top:2850px;background:linear-gradient(135deg,#2f4a3a,#6f8a6a 45%,#c98b4e)" role="img" aria-label="House with lit patio at dusk"></div>
<div class="abs date-badge" style="left:473px;top:2948px"><b>20</b><span>DEC</span></div>
<article class="abs post-body" style="top:2840px">
  <h3>Lorem ipsum dolor amet eiusmod consectetur adipiscing elit eiusmod tempor.</h3>
  <p>Lorem ipsum dolor sit amet, consectetur adipiscing elit, sed do eiusmod tempor incididunt ut labore et dolore magna aliqua. Ut enim ad minim veniam, quis nostrud exercitation ullamco laboris nisi ut aliquip ex ea commodo consequat. Duis aute irure dolor in reprehenderit in voluptate velit esse cillum dolore...</p>
  <a class="btn-pill btn-outline">Read more <svg width="12" height="12" viewBox="0 0 12 12"><circle cx="6" cy="6" r="6" fill="#f0555c"/><path d="M5 3.5 7.5 6 5 8.5" fill="none" stroke="#fff" stroke-width="1.6"/></svg></a>
</article>

<section class="abs newsletter">
  <h2>Stay up to date with us</h2>
  <p>Lorem ipsum dolor sit amet, consectetur adipiscing elit, sed do eiusmod tempor...</p>
  <div class="news-field">Enter Email Address</div>
  <div class="news-btn">Join us</div>
</section>

<footer class="abs site-footer"></footer>
<h3 class="abs foot-title" style="left:110px;top:3503px">Contact us</h3>
<ul class="abs contact-list">
  <li><svg width="14" height="18" viewBox="0 0 14 18"><path d="M7 1a6 6 0 0 1 6 6c0 4-6 10-6 10S1 11 1 7a6 6 0 0 1 6-6z" fill="#fff"/><circle cx="7" cy="7" r="2.2" fill="#177079"/></svg><span>12-04 Laman Seri, Jalan Cempaka, Taman Pelangi, 80400 Johor Bahru.</span></li>
  <li><svg width="14" height="14" viewBox="0 0 14 14"><path d="M3 1l2.5 3-1.5 1.5a8 8 0 0 0 4.5 4.5L10 8.5l3 2.5-1.5 2C6 13 1 8 1 2.5z" fill="#fff"/></svg><span>+60 7 555 0142</span></li>
  <li><svg width="14" height="12" viewBox="0 0 14 12"><rect x="0" y="1" width="14" height="10" fill="#fff"/><path d="M0 1l7 5 7-5" fill="none" stroke="#177079" stroke-width="1.4"/></svg><span>hello@meadowkrcircle.example</span></li>
</ul>
<h3 class="abs foot-title" style="left:398px;top:3503px">Quick contact</h3>
<div class="abs field" style="left:398px;top:3557px;width:155px;height:36px">Name</div>
<div class="abs field" style="left:571px;top:3557px;width:154px;height:36px">Email</div>
<div class="abs field" style="left:398px;top:3606px;width:327px;height:64px">Message</div>
<div class="abs submit">Submit</div>
<div class="abs map" role="img" aria-label="Street map showing the office location"><span class="map-tag">➜ Get Direction</span></div>
<div class="abs foot-rule"></div>
<div class="abs copyright">Copyrights © 2018 Meadow Kr Circle. All Rights Reserved.</div>
<div class="abs social" aria-label="Social links"><span></span><span></span><span></span><span></span></div>

</body>
</html>
```